Business Card design for law firm = Brightvale Australia

We are seeking a new design for our business cards.
We are keeping our logo, which is attached.
We need space for
Name
Title
Address is , which is
Level 7
214 Marlowe Street
Sydney NSW 2047
Phone :
Mobile :
Fax :
Email :
DX :
website www.brightvale-example.com.au

Industry/Entity Type

Law Firm / Banking and Finance

Contact Information for Business Card

We are seeking a new design for our business cards. We are keeping our logo. We need space for Name Title Address is Level 7 214 Marlowe Street Sydney NSW 2047 Phone Mobile Fax Email DX website www.brightvale-example.com.au

Colors
0054AA
0677BA
7BADD7
CADEEF
E8F1F8

Requirements
Must have
• see our website for general feel www.brightvale-example.com.au

```html
<!DOCTYPE html>
<html lang="en">
<head>
<meta charset="utf-8">
<title>Brightvale Australia – Business Card</title>
<link rel="stylesheet" href="https://fonts.googleapis.com/css2?family=EB+Garamond:wght@400;500&family=Open+Sans:wght@300;400&display=swap">
<style>
  :root {
    --backdrop: #2b2b2b;
    --navy: #2e4f98;
    --navy-deep: #2a4a91;
    --navy-light: #33569f;
    --teal: #0a8dc6;
    --teal-soft: #1a8fc4;
    --ink: #22408f;
    --text: #2a2a2a;
    --paper: #f3f3f3;
    --paper-shade: #e2e2e2;
    --white: #f4f4f4;
  }
  * { margin: 0; padding: 0; box-sizing: border-box; }
  html, body { width: 1200px; height: 1138px; overflow: hidden; }
  body { background: var(--backdrop); position: relative; font-family: "EB Garamond", Georgia, serif; }

  .card {
    position: absolute;
    border-radius: 18px;
    overflow: hidden;
  }

  /* Front */
  .card-front {
    left: 272px; top: 184px; width: 622px; height: 376px;
    background: linear-gradient(180deg, var(--navy-deep) 0%, var(--navy-light) 100%);
  }
  .card-front .brand-square {
    position: absolute; left: 263px; top: 94px; width: 81px; height: 81px;
    background: var(--teal);
  }
  .card-front .brand-name {
    position: absolute; left: 0; width: 100%; top: 178px;
    text-align: center; font-size: 50px; line-height: 1; font-weight: 400;
    color: var(--white);
  }
  .card-front .tagline {
    position: absolute; left: 0; width: 100%; top: 236px;
    text-align: center; font-family: "Open Sans", Arial, sans-serif; font-weight: 300;
    font-size: 18px; letter-spacing: 1.6px; color: var(--teal-soft);
  }
  .card-front .website {
    position: absolute; left: 0; width: 100%; top: 332px;
    text-align: center; font-size: 15px; letter-spacing: 6px; color: var(--white);
  }
  .card-front .base-bar {
    position: absolute; left: 142px; bottom: 0; width: 340px; height: 9px;
    background: var(--teal);
  }

  /* Back */
  .card-back {
    left: 274px; top: 606px; width: 619px; height: 375px;
    background: linear-gradient(180deg, var(--paper) 0%, var(--paper-shade) 100%);
  }
  .person-name {
    position: absolute; left: 32px; top: 68px;
    font-size: 26px; line-height: 1; color: var(--ink);
  }
  .person-title {
    position: absolute; left: 32px; top: 100px;
    font-size: 16px; color: var(--text);
  }
  .card-back .brand-square {
    position: absolute; left: 320px; top: 44px; width: 82px; height: 82px;
    background: var(--teal);
  }
  .card-back .brand-name {
    position: absolute; left: 318px; top: 146px;
    font-size: 50px; line-height: 1; color: var(--ink);
  }
  .address {
    position: absolute; left: 34px; top: 208px;
    font-size: 16px; line-height: 20px; color: var(--text); font-style: normal;
  }
  .contact-list {
    position: absolute; left: 38px; top: 259px; list-style: none;
    font-size: 15.5px; line-height: 20px; color: var(--text);
  }
  .contact-list li { display: flex; align-items: center; }
  .contact-list svg { width: 12px; height: 12px; margin-right: 14px; fill: var(--teal); flex: none; }
  .tagline-tab {
    position: absolute; left: 280px; top: 328px; width: 339px; height: 47px;
    background: var(--teal);
    clip-path: polygon(22px 0, 100% 0, 100% 100%, 0 100%);
    font-family: "Open Sans", Arial, sans-serif; font-size: 15px; letter-spacing: 1.3px;
    color: var(--white); padding: 13px 0 0 62px;
  }
</style>
</head>
<body>

<section class="card card-front" aria-label="Card front">
  <div class="brand-square"></div>
  <div class="brand-name">Brightvale</div>
  <div class="tagline">strategic legal outsourcing</div>
  <div class="website">www.brightvale-example.com.au</div>
  <div class="base-bar"></div>
</section>

<section class="card card-back" aria-label="Card back">
  <div class="person-name">Sam Whitford</div>
  <div class="person-title">Managing Director</div>

  <div class="brand-square"></div>
  <div class="brand-name">Brightvale</div>

  <address class="address">Level 7 214 Marlowe Street<br>Sydney NSW 2047</address>

  <ul class="contact-list">
    <li>
      <svg viewBox="0 0 12 12" aria-hidden="true"><path d="M1 3.5C1 2 3 1.5 6 1.5S11 2 11 3.5v1H8.5v-1h-5v1H1z"/><path d="M3 5h6l2 5H1z"/></svg>
      02 9000 4187
    </li>
    <li>
      <svg viewBox="0 0 12 12" aria-hidden="true"><rect x="3" y="1" width="6" height="3"/><rect x="1" y="4.5" width="10" height="4.5" rx="1"/><rect x="3" y="8" width="6" height="3"/></svg>
      02 9000 4190
    </li>
    <li>
      <svg viewBox="0 0 12 12" aria-hidden="true"><path d="M1 2.5h10v7H1z M1.6 3 6 6.6 10.4 3" fill="none" stroke="#0a8dc6" stroke-width="1.2"/><path d="M1 2.5h10L6 6.5z"/></svg>
      sam.whitford@brightvale-example.com.au
    </li>
    <li>
      <svg viewBox="0 0 12 12" aria-hidden="true"><circle cx="6" cy="6" r="5" fill="none" stroke="#0a8dc6" stroke-width="1.2"/><path d="M1 6h10M6 1v10" stroke="#0a8dc6" stroke-width="1"/><ellipse cx="6" cy="6" rx="2.2" ry="5" fill="none" stroke="#0a8dc6" stroke-width="1"/></svg>
      www.brightvale-example.com.au
    </li>
  </ul>

  <div class="tagline-tab">strategic legal outsourcing</div>
</section>

</body>
</html>
```